Falkrin homes and renovations business card design.

Would like some new card designs utilizing my new logo that look professional. I am open to different colors on the logo or utilize the same ones we have. I like the original concept but would like to see some fresh ideas and build on what we have already done.

Target Market(s)

Custom home building industry, Real estate sales, Renovation projects.

Industry/Entity Type

Home Builder

Contact Information for Business Card

Falkrin Homes and Renovations
2871 96th Avenue
Ashby, Norvale
T2R3W8
Home : 403- 718-4063 Cell: 403- 294-5170

My info is : Dax Falkrin, President and CEO
email: falkrinhomes@maildrop-example.net
Website: falkrinhomes-example.com
websit

Requirements
Must have
• Must Use my new logo design. I am open to different colors on the logo or utilize the same ones in the existing design. I can upload the original logo design if needed.

```html
<!DOCTYPE html>
<html lang="en">
<head>
<meta charset="utf-8">
<title>Falkrin Homes and Renovations – Business Card</title>
<link href="https://fonts.googleapis.com/css2?family=Raleway:wght@400;500&family=Montserrat:wght@600&display=swap" rel="stylesheet">
<style>
  :root {
    --backdrop: #d6d7d9;
    --card-white: #ffffff;
    --charcoal: #414042;
    --yellow: #f9bc15;
    --gold: #b8892e;
    --muted: #7a7a7c;
    --ink-light: #ffffff;
  }
  * { box-sizing: border-box; margin: 0; padding: 0; }
  html, body { width: 1200px; height: 800px; overflow: hidden; }
  body { background: var(--backdrop); font-family: "Raleway", sans-serif; position: relative; }

  .card { position: absolute; left: 345px; width: 510px; height: 283px; overflow: hidden; }
  .card--front { top: 70px; background: var(--card-white); }
  .card--back { top: 410px; background: var(--charcoal); }

  .brand { position: absolute; display: flex; flex-direction: column; align-items: center; text-align: center;
           font-family: "Montserrat", sans-serif; font-weight: 600; color: var(--gold); line-height: 1.15; }
  .brand__mark { flex: none; background: var(--gold); }
  .card--front .brand { left: 8px; width: 200px; top: 100px; font-size: 16px; gap: 12px; }
  .card--front .brand__mark { width: 22px; height: 22px; }
  .card--back .brand { left: 0; right: 0; top: 84px; font-size: 24px; gap: 18px; }
  .card--back .brand__mark { width: 32px; height: 32px; }

  .details { position: absolute; left: 242px; top: 0; width: 268px; height: 283px; background: var(--charcoal); }
  .details__bar { position: absolute; left: 0; right: 0; height: 11px; background: var(--yellow); }
  .details__bar--top { top: 0; }
  .details__bar--bottom { bottom: 0; }

  .person { position: absolute; top: 28px; left: 0; right: 0; text-align: center; }
  .person__name { font-size: 26px; font-weight: 500; color: var(--yellow); line-height: 1; }
  .person__title { font-size: 13px; color: var(--muted); margin-top: 3px; }

  .contact { position: absolute; left: 9px; display: flex; align-items: center; gap: 14px;
             color: var(--ink-light); font-size: 15px; line-height: 1.3; white-space: nowrap; }
  .contact__icon { width: 27px; height: 27px; border-radius: 50%; background: var(--yellow);
                   display: flex; align-items: center; justify-content: center; flex: none; }
  .contact--phone { top: 90px; }
  .contact--address { top: 137px; }
  .contact--email { top: 188px; font-size: 12px; }
  .contact--web { top: 235px; font-size: 13.5px; }
</style>
</head>
<body>
  <section class="card card--front" aria-label="Card front">
    <div class="brand"><span class="brand__mark"></span><span>Falkrin<br>Homes and Renovations</span></div>
    <div class="details">
      <div class="details__bar details__bar--top"></div>
      <div class="person">
        <p class="person__name">Dax Falkrin</p>
        <p class="person__title">President and CEO</p>
      </div>
      <div class="contact contact--phone">
        <span class="contact__icon"><svg width="14" height="16" viewBox="0 0 14 16"><rect x="3.5" y="1" width="7" height="14" rx="1.5" fill="none" stroke="#414042" stroke-width="1.4"/><line x1="6" y1="12.5" x2="8" y2="12.5" stroke="#414042" stroke-width="1.2"/></svg></span>
        <span>403- 718-4063<br>403- 294-5170</span>
      </div>
      <div class="contact contact--address">
        <span class="contact__icon"><svg width="14" height="16" viewBox="0 0 14 16"><path d="M7 15C7 15 2 9.5 2 6a5 5 0 0 1 10 0c0 3.5-5 9-5 9z" fill="#414042"/><circle cx="7" cy="6" r="1.8" fill="#f9bc15"/></svg></span>
        <span>2871 96th Avenue<br>Ashby, Norvale</span>
      </div>
      <div class="contact contact--email">
        <span class="contact__icon"><svg width="16" height="12" viewBox="0 0 16 12"><rect x="1" y="1" width="14" height="10" fill="none" stroke="#414042" stroke-width="1.3"/><path d="M1 1l7 6 7-6" fill="none" stroke="#414042" stroke-width="1.3"/></svg></span>
        <span>falkrinhomes@maildrop-example.net</span>
      </div>
      <div class="contact contact--web">
        <span class="contact__icon"><svg width="16" height="16" viewBox="0 0 16 16"><circle cx="8" cy="8" r="6.5" fill="none" stroke="#414042" stroke-width="1.3"/><ellipse cx="8" cy="8" rx="3" ry="6.5" fill="none" stroke="#414042" stroke-width="1"/><line x1="1.5" y1="8" x2="14.5" y2="8" stroke="#414042" stroke-width="1"/></svg></span>
        <span>www.falkrinhomes-example.com</span>
      </div>
      <div class="details__bar details__bar--bottom"></div>
    </div>
  </section>

  <section class="card card--back" aria-label="Card back">
    <div class="brand"><span class="brand__mark"></span><span>Falkrin<br>Homes and Renovations</span></div>
  </section>
</body>
</html>
```